DL Flyer for vehicle buying/selling service and advice business

New business to help people sell their current vehicle then select and buy and maintain their next car. (New or used).
We'll prepare and sell your car for you and get $,000s more than a trade in.
Offer advice as to the best car currently on the market based on our customer's needs.
With country wide sourcing network of cars across all manufacturers we have great buying power to ensure the very best possible price.
Personal service, including preparation of car for sale, pickup of old and drop-off of new vehicles, organise RWC and any required repairs.
We are NOT a car dealer so we WILL not try to sell you the vehicles we own.
Totally impartial, professional and friendly service making the purchase of your next car a great experience.

Flyer wording===========“Don’t sell your car or buy your next car without speaking to us”We guarantee to get you a better price for your current car and to find a cheaper purchase price for your next car.With a country wide sourcing network of cars “new and used” across all manufacturers we have sensational buying power to ensure the very best possible price.We can source the right car on any budget, from $2,000 to $200,000We are NOT a car dealer so we WILL not try to sell you the vehicles we own.By not being affiliated with any individual car manufacturer or dealer we can offer absolute impartiality.We’ll sit with you to discuss the best car for your needs and even bring the car to you for a test drive without the pressure of a salesperson nearby.Our services include:• Selling your current car: - Obtaining a roadworthy certificate - Organising any repairs needed - Detailing your car (wash, vacuum, polish) - Advertising of your car - Dealing with potential buyers - Negotiating the best price on your behalf• Assisting with the selection of your next car• Organising test drives• Purchasing the car of your choice - Sourcing the very best price• Ongoing management of their vehicle (service, clean, repair)Possible inclusions in the flyer might be:Advantages of upgrading to a new vehicle include:o reliability, o safety,o fuel efficiencyo comfort.Space for a couple of short testimonials Background images of all of the major car manufacturers Added Friday, July 29, 2016

Target Market(s)

Local community.
Initially will drop DL flyers in local post boxes

Industry/Entity Type

Business

Requirements
Must have
• Flyer wording:
• ===========
• “Don’t sell your car or buy your next car without speaking to us”
• ---------------------------------------------------------------------------------
• We guarantee to get you a better price for your current car and to find a cheaper purchase price for your next car.
• With a country wide sourcing network of cars “new and used” across all manufacturers we have sensational buying power to ensure the very best possible price.
• We can source the right car on any budget, from $2,000 to $200,000
• We are NOT a car dealer so we WILL not try to sell you the vehicles we own.
• By not being affiliated with any individual car manufacturer or dealer we can offer absolute impartiality.
• We’ll sit with you to discuss the best car for your needs and even bring the car to you for a test drive without the pressure of a salesperson nearby.
• Our services include:
• • Selling your current car:
• o Obtaining a roadworthy certificate
• o Organising any repairs needed
• o Detailing your car (wash, vacuum, polish)
• o Advertising of your car
• o Dealing with potential buyers
• o Negotiating the best price on your behalf
• • Assisting with the selection of your next car
• • Organising test drives
• • Purchasing the car of your choice
• o Sourcing the very best price
• • Ongoing management of your vehicle (service, clean, repair)
• Call Gerald on: 0427 315904
Nice to have
• Possible inclusions on the flyer might be:
• List of advantages of upgrading to a new vehicle:
• o reliability,
• o safety,
• o fuel efficiency
• o comfort
• Space for a couple of short testimonials
• Background images of all of the major car manufacturers

```html
<!DOCTYPE html>
<html lang="en">
<head>
<meta charset="utf-8">
<title>Kerbside – DL Flyer</title>
<link rel="stylesheet" href="https://fonts.googleapis.com/css2?family=Oswald:wght@300;400;500;600&family=Open+Sans:wght@400;600;700&display=swap">
<style>
  :root{
    --orange:#ff5a00;
    --orange-light:#ff7a1a;
    --charcoal:#2b2b2b;
    --ink:#333333;
    --paper:#f1f1f1;
    --paper-dark:#d9d9d9;
    --stage:#eeeeee;
    --white:#ffffff;
  }
  *{box-sizing:border-box;margin:0;padding:0}
  html,body{width:1200px;height:1200px;overflow:hidden;background:var(--stage)}
  .canvas{position:relative;width:1200px;height:1200px}
  .flyer{position:absolute;top:129px;width:471px;height:943px;overflow:hidden;
    background:linear-gradient(180deg,var(--paper-dark) 0%,var(--paper) 45%,var(--paper-dark) 100%);
    font-family:"Open Sans",Arial,sans-serif;color:var(--ink)}
  .flyer--front{left:100px}
  .flyer--back{left:628px}
  .shapes{position:absolute;inset:0}

  .brand{position:absolute;left:0;right:0;display:flex;justify-content:center;align-items:center;gap:12px;
    font-family:"Oswald",sans-serif;font-weight:600;font-size:66px;letter-spacing:2px;color:var(--charcoal);line-height:1}
  .brand__mark{width:22px;height:22px;background:var(--orange)}
  .flyer--front .brand{top:365px}
  .flyer--back .brand{top:42px}

  .offer-box{position:absolute;left:32px;top:488px;width:407px;height:168px;border-radius:14px;
    background:linear-gradient(180deg,var(--orange-light),var(--orange));
    padding:27px 0 0 24px;font-family:"Oswald",sans-serif;font-weight:500;color:var(--charcoal);
    font-size:31px;line-height:37px;text-transform:uppercase;white-space:nowrap}
  .offer-box__line{display:block}
  .offer-box__sub{display:block;font-size:28px;margin-top:2px}

  .tagline{position:absolute;left:0;right:0;top:700px;text-align:center;font-family:"Oswald",sans-serif;color:var(--charcoal);white-space:nowrap}
  .tagline__main{display:block;font-size:37px;font-weight:400;line-height:42px}
  .tagline__rest{display:block;font-size:26px;font-weight:300;line-height:30px}

  .body-copy{position:absolute;left:32px;width:407px;font-size:12.6px;line-height:16.5px;text-align:justify}
  .flyer--front .body-copy{top:798px}
  .flyer--back .body-copy{top:246px;font-weight:700;color:var(--charcoal);text-align-last:center}

  .headline{position:absolute;left:0;right:0;top:163px;text-align:center;font-family:"Oswald",sans-serif;
    font-weight:400;font-size:31px;line-height:35px;color:var(--white);white-space:nowrap}

  .call-band{position:absolute;left:0;bottom:0;width:100%;height:47px;background:var(--charcoal);border-top:4px solid var(--orange)}
  .call-pill{position:absolute;left:52px;top:872px;width:367px;height:48px;border-radius:24px;background:var(--orange);
    color:var(--white);font-family:"Oswald",sans-serif;font-weight:400;font-size:28px;line-height:48px;text-align:center;
    white-space:nowrap;box-shadow:0 0 0 3px var(--white)}

  .services-title{position:absolute;left:0;right:0;top:510px;text-align:center;font-family:"Oswald",sans-serif;
    font-weight:500;font-size:31px;color:var(--orange);text-decoration:underline;text-underline-offset:3px}
  .section-title{position:absolute;left:0;right:0;text-align:center;font-weight:600;font-size:17px;color:#111;white-space:nowrap}
  .section-title--selling{top:562px}
  .section-title--advantages{top:705px;font-size:16.5px}

  .bullets{position:absolute;list-style:none;font-family:"Oswald",sans-serif;font-weight:300;font-size:11.6px;line-height:16.4px;color:#111;white-space:nowrap}
  .bullets li{position:relative;padding-left:14px}
  .bullets li::before{content:"";position:absolute;left:0;top:5px;width:7px;height:7px;border-radius:50%;background:var(--orange)}
  .bullets--selling{left:38px;top:596px}
  .bullets--next{left:238px;top:596px}
  .bullets--advantages{left:38px;top:744px}

  .photo-frame{position:absolute;left:152px;top:744px;width:278px;height:110px;border-radius:22px;border:4px solid var(--orange);
    background:linear-gradient(135deg,#7fa35a,#c9b48e 55%,#e3e0dc)}
</style>
</head>
<body>
<main class="canvas">

  <section class="flyer flyer--front">
    <svg class="shapes" viewBox="0 0 471 943" aria-hidden="true">
      <polygon points="0,365 471,222 471,235 0,390" fill="#ffffff"/>
      <polygon points="0,318 471,206 471,224 0,366" fill="#ff5a00"/>
      <polygon points="150,320 471,238 471,246 190,316" fill="#2b2b2b"/>
    </svg>
    <svg class="shapes" viewBox="0 0 471 943" role="img" aria-label="Photo: smiling woman holding car keys beside an open car door with a friend, on a city street">
      <defs>
        <linearGradient id="frontPhoto" x1="0" y1="0" x2="1" y2="1">
          <stop offset="0" stop-color="#b9b2a8"/>
          <stop offset="0.5" stop-color="#6e5f55"/>
          <stop offset="1" stop-color="#3a3836"/>
        </linearGradient>
      </defs>
      <polygon points="0,0 471,0 471,204 0,312" fill="url(#frontPhoto)"/>
    </svg>

    <div class="brand"><span class="brand__mark"></span>KERBSIDE</div>

    <div class="offer-box">
      <span class="offer-box__line">Before you sell your car</span>
      <span class="offer-box__line">or buy a new car call us..</span>
      <span class="offer-box__sub">We will get you a better price</span>
    </div>

    <h1 class="tagline">
      <span class="tagline__main">Don’t sell your car or buy</span>
      <span class="tagline__rest">your next car without speaking to us</span>
    </h1>

    <p class="body-copy">We guarantee to get you a better price for your current car and to find a cheaper purchase price for your next car. With a country wide sourcing network of cars “new and used” across all manufacturers we have sensational buying power to ensure the very best possible price</p>

    <div class="call-band"></div>
    <div class="call-pill">CALL GERALD ON: 0427 315904</div>
  </section>

  <section class="flyer flyer--back">
    <svg class="shapes" viewBox="0 0 471 943" role="img" aria-label="Faded photo of a smiling couple, tinted orange">
      <defs>
        <linearGradient id="backPhoto" x1="0" y1="0" x2="1" y2="1">
          <stop offset="0" stop-color="#ff4f00"/>
          <stop offset="0.6" stop-color="#ff6a10"/>
          <stop offset="1" stop-color="#ff7d2a"/>
        </linearGradient>
      </defs>
      <polygon points="0,0 471,0 471,490 0,370" fill="url(#backPhoto)"/>
    </svg>
    <svg class="shapes" viewBox="0 0 471 943" aria-hidden="true">
      <polygon points="0,370 471,490 471,528 0,418" fill="#2b2b2b"/>
      <polygon points="60,420 471,525 471,532 90,434" fill="#ffffff"/>
    </svg>

    <div class="brand"><span class="brand__mark" style="background:var(--white)"></span>KERBSIDE</div>

    <h2 class="headline">We can source the right car on any<br>budget, from $2,000 to $200,000</h2>

    <p class="body-copy">We are NOT a car dealer so we WILL not try to sell you the vehicles we own. By not being affiliated with any individual car manufacturer or dealer we can offer absolute impartiality. We’ll sit with you to discuss the best car for your needs and even bring the car to you for a test drive without the pressure of a salesperson nearby.</p>

    <h3 class="services-title">OUR SERVICES</h3>
    <h4 class="section-title section-title--selling">Selling your current car:</h4>

    <ul class="bullets bullets--selling">
      <li>Obtaining a roadworthy certificate</li>
      <li>Organising any repairs needed</li>
      <li>Detailing your car (wash, vacuum, polish)</li>
      <li>Advertising of your car</li>
      <li>Dealing with potential buyers</li>
      <li>Negotiating the best price on your behalf</li>
    </ul>
    <ul class="bullets bullets--next">
      <li>Assisting with the selection of your next car</li>
      <li>Organising test drives</li>
      <li>Purchasing the car of your choice</li>
      <li>Sourcing the very best price</li>
      <li>Ongoing management of your vehicle<br>(service, clean, repair)</li>
    </ul>

    <h4 class="section-title section-title--advantages">List of advantages of upgrading to a new vehicle:</h4>
    <ul class="bullets bullets--advantages">
      <li>Reliability</li>
      <li>Safety</li>
      <li>Fuel efficiency</li>
      <li>Comfort</li>
      <li>Space for a couple<br>of short testimonials</li>
    </ul>
    <div class="photo-frame" role="img" aria-label="Photo: family with grandparents, children and a dog sitting in the open boot of a car in a park"></div>

    <div class="call-band"></div>
    <div class="call-pill">CALL GERALD ON: 0427 315904</div>
  </section>

</main>
</body>
</html>
```